Edgey, Modern Air Conditioning Website

Bramble Works
current website - www.kelvaroom.nz
Friendlane - www.facebook.com/bramwrk

We really have no idea about webdesign etc we are Engineers not Graphic artists or creative writers. We really just want a edgy, modern website completed on our behalf

We can get pictures of projects as directed or happy for you to use stock images of Talvoro Mecha NZ (Heatpumps) air conditioning and exposed ducting etc

we would like the website to be heavily based on the below website. I like what they have done with both the site and the app but obviously would need to suit Bramble Works, snowflakes heating cooling etc etc Blue and white to match our logo etc

http://parrowbeams.co.nz/

Need links to contact page:
Bramble Works
27 Harlow Crescent
Petone
Wellington

0800 529 174 (0800BRAMWKS)

Marta.k@bramwks.co.nz

BRAMBLE WORKS
SATISFACTION GAURANTEED

WHY CHOOSE BRAMBLE WORKS
EXPERIENCE COUNTS

We have a team of nationally trained and qualified Refrigeration/HVAC/Electrical Engineers and Technicians based in Petone, Wellington offering services to Wellington, Manuwatu and the Wairarapa. We are factory trained and authorised to design, service and install all major brands including Talvoro, Pelnor, Korrowane Electric, Veltrada and Osmelo units. We extend our installation warranty to match that of the manufacturer’s warranty and specialise in our own diagnostics and repair.

SATISFACTION GUARANTEE
We aim to please and I put my name behind our brand! We will take care of your project from start to finish and offer a unique experience with our 100% satisfaction Guarantee*. We will supply and install your system and if your system is not installed how it was explained or not up to a trades standard we will return to make any the necessary modifications free of charge. We back this service up with our 0% upfront strategy, the power is in your hands. We will only invoice you once the installation has been completed up to a BRAMBLE WORKS standard.

LOW PRESSURE SALES
Nobody likes the vacuum salesmen’s techniques and neither do we. We will come to your home or business to provide a free measure and quote. Our experience will insure this is a quick and painless experience, you will be provided with expert advice from a qualified Refrigeration Engineer, not a car salesmen turned “Heating Guru”. We will follow up with an email providing our best price straight up, installation details and online brochures. We won’t bug you with repeated phone calls and inbox clogging emails. Once we receive confirmation we will issue you with an installation date and typically have your installation completed within 10 working days.

BRANDS
www.talvoromecha.co.nz
www.pelnor.co.nz
http://quellaro.co.nz/

SERVICES
Heatpumps/Air Conditioning – Heat pumps are the most efficient way of using electricity to heat your home, but some are more efficient than others. We will select the right model for your requirements taking into account the capacity required, the visual impact of the system, the style of system, air flow and obviously your personal preferences. We only install the highest quality brands that offer outstanding after sales support. Cassettes, Consoles, Under Ceilings, Ducted, Hiwalls, Multis… Confused? Give us a call.

COMMERCIAL
We have a growing Portfolio of clients that rely on us for their Commercial requirements. We have proven ourselves to be a force to be reckoned with to be able to think outside the square and come up with unique and cost effective solutions to heat and cool large areas.

CENTRAL HEATING
Ducted Heatpumps are the holy grail of central heating and guess what? They can also cool and dehumidify your home. Ducted Heatpumps are often overlooked or priced out of reach by less experienced salesmen as its not just a point and shoot approach. We pride ourselves in our work with Ducted systems, we are able to provide quick and economic quotations and can provide expert advice on all the extra options on Ducted systems with zone control, fresh air integration, positive pressure solutions. We use the best materials when it comes to insulated ducting, mounting equipment, drainage materials. Every system we design is designed with the lowest possible decibel reading, least amount of static pressure and maximum effieciency with the help of the very latest software available.

VENTILATION
Home ventilation is a very important part of insuring you have a nice dry home to maximise the efficiency of your Heat pump. Whilst HRV systems are not designed to Heat your house they are designed to keep it dry, provide fresh filtered air to ensure your home healthy and easy to heat. We offer a number of solutions from integrated ducted heatpump systems to balanced heat recovery systems and positive air systems.

TESTIMONIALS
http://www.lotbazaro.co.nz/Browse/Listing.aspx?id=415728306

Target Market(s)

Home Owners

Industry/Entity Type

Air Conditioning

Colors
33a6d7
ffffff

Requirements
Must have
• Could possibly use the 'O' from Bramble Works logo throughout website - see business Card
Nice to have
• Bright & Crisp - White and Blue
• Would love to have our Logo used throughout the website.

```html
<!DOCTYPE html>
<html lang="en">
<head>
<meta charset="utf-8">
<title>Bramble Works – Heating &amp; Cooling</title>
<link rel="stylesheet" href="https://fonts.googleapis.com/css2?family=Lato:wght@300;400;700;900&family=Oswald:wght@300;400&display=swap">
<style>
:root{
  --blue:#33a6d7;
  --blue-dark:#2a93c2;
  --ink:#222a30;
  --text:#555e66;
  --muted:#8a9298;
  --white:#ffffff;
  --grey-band:#e8ebee;
  --footer:#2b3238;
  --line:#d6dadd;
}
*{box-sizing:border-box;margin:0;padding:0}
html,body{width:1200px;height:3822px;overflow:hidden;background:var(--white)}
body{font-family:"Lato",sans-serif;color:var(--text);position:relative}
.abs{position:absolute}
.section{position:absolute;left:0;width:1200px}

/* header / hero */
.hero{top:0;height:600px;background:linear-gradient(180deg,#3b4a55 0%,#5b6a74 40%,#44525c 100%)}
.hero-photo{position:absolute;inset:0;background:linear-gradient(135deg,#4d5c66 0%,#7d8a92 45%,#3a4852 100%)}
.hero-shade{position:absolute;left:0;top:0;width:1200px;height:160px;background:linear-gradient(180deg,rgba(20,28,34,.7),rgba(20,28,34,0))}
.brand{left:100px;top:14px;color:var(--white);font-weight:900;font-size:40px;letter-spacing:2px;line-height:1}
.brand-sub{left:100px;top:58px;color:var(--white);font-weight:900;font-size:14px;letter-spacing:9px}
.callout{left:888px;top:26px;display:flex;align-items:center;gap:12px;color:var(--white)}
.callout-badge{width:50px;height:50px;border:3px solid var(--white);border-radius:50%;display:flex;align-items:center;justify-content:center;font-weight:900;font-size:14px}
.callout-num{font-weight:700;font-size:26px;line-height:1.05}
.callout-note{font-weight:700;font-size:14px;letter-spacing:.5px}
.nav{left:96px;top:110px;width:1010px;display:flex;justify-content:space-between;align-items:center}
.nav a{color:var(--white);text-decoration:none;font-weight:700;font-size:15px;display:flex;align-items:center;gap:12px;letter-spacing:.3px}
.nav a.active{color:var(--blue)}
.nav svg{width:28px;height:26px}
.nav-dot{left:142px;top:142px;width:8px;height:8px;border-radius:50%;background:var(--white)}
.hero-title{left:0;width:1200px;top:318px;text-align:center;color:var(--white);font-family:"Oswald",sans-serif;font-weight:300;font-size:35px;line-height:48px;letter-spacing:1px}
.dots{display:flex;gap:8px}
.dots span{width:11px;height:11px;border-radius:50%;background:#c9d0d5}
.dots span.on{background:var(--blue)}
.hero .dots{left:570px;top:562px}
.hero .dots span{background:rgba(255,255,255,.6)}
.hero .dots span.on{background:var(--blue)}

/* section titles */
.title{left:0;width:1200px;text-align:center;font-weight:700;font-size:33px;color:var(--ink);letter-spacing:1px}
.title b{color:var(--blue);font-weight:700}
.rule{left:400px;width:400px;height:1px;background:var(--line)}
.rule::after{content:"";position:absolute;left:170px;top:-1px;width:60px;height:3px;background:var(--blue)}
.on-blue .title{color:var(--white)}
.on-blue .rule{background:rgba(255,255,255,.45)}
.on-blue .rule::after{background:var(--white)}

/* why choose */
.why{top:600px;height:763px}
.why-intro{left:130px;width:940px;top:124px;text-align:center;font-size:15px;line-height:26px;color:var(--text)}
.why-band{left:0;top:279px;width:1200px;height:484px;background:var(--blue)}
.why-photo{top:210px;width:311px;height:242px;border:4px solid var(--white);box-shadow:0 2px 6px rgba(0,0,0,.15)}
.why-head{top:492px;width:311px;text-align:center;color:var(--white);font-weight:700;font-size:19px;letter-spacing:.5px}
.why-text{top:520px;width:311px;color:var(--white);font-size:12px;line-height:17px;text-align:center}

/* about */
.about{top:1363px;height:362px}
.about-img{left:97px;top:127px;width:387px;height:141px;background:linear-gradient(160deg,#c9d7e3,#8fb0c9 60%,#d9e2e8)}
.about-text{left:510px;top:150px;width:600px;font-size:14px;line-height:25px;color:var(--text)}
.btn-outline{display:inline-flex;align-items:center;gap:6px;border:1px solid var(--blue);color:var(--blue);font-weight:700;font-size:12px;padding:7px 14px;letter-spacing:.5px}
.about .btn-outline{position:absolute;left:510px;top:290px}

/* services */
.services{top:1725px;height:522px;background:var(--blue)}
.svc{top:160px;width:260px;text-align:center;color:var(--white)}
.svc-icon{width:144px;height:144px;margin:0 auto;display:block}
.svc h3{font-weight:700;font-size:19px;margin-top:20px;letter-spacing:.5px}
.svc p{font-size:12.5px;line-height:17px;margin:10px auto 0;width:230px}
.btn-white{display:inline-flex;align-items:center;gap:5px;background:var(--white);color:var(--blue);font-weight:700;font-size:12px;padding:6px 12px;margin-top:16px}

/* testimonials */
.testimonials{top:2247px;height:556px}
.person{top:170px;width:320px;text-align:center}
.avatar{width:88px;height:88px;border-radius:50%;margin:0 auto;border:4px solid var(--white);box-shadow:0 0 0 3px var(--blue);background:linear-gradient(160deg,#c8ced3,#8b959c)}
.person-name{margin-top:12px;font-size:13px;font-weight:700;color:var(--ink)}
.person-handle{font-size:12px;color:var(--blue);margin-top:4px}
.quote{top:339px;width:318px;height:128px;border:1px solid var(--line);background:var(--white);padding:18px 22px 0 40px;font-size:13px;line-height:19px;color:var(--text)}
.quote.current{border-bottom:3px solid var(--blue)}
.quote-mark{position:absolute;left:12px;top:14px;font-size:34px;line-height:1;color:var(--blue);font-weight:900}
.quote-mark.end{left:auto;right:12px;top:62px}
.quote-date{position:absolute;left:40px;bottom:10px;font-size:10px;color:var(--muted)}
.testimonials .dots{left:577px;top:502px}

/* gallery */
.gallery{top:2803px;height:356px;background:var(--grey-band)}
.tile{top:170px;width:224px;height:136px;border:3px solid var(--white)}
.tile-caption{position:absolute;inset:0;background:rgba(25,32,38,.72);color:var(--white);text-align:center;padding-top:26px}
.tile-caption strong{display:block;font-size:15px;font-weight:700}
.tile-caption span{display:block;font-size:12px;line-height:16px;margin-top:8px;padding:0 18px}
.arrow{top:228px;width:20px;height:24px}

/* brands */
.brands{top:3159px;height:344px}
.brand-row{left:100px;top:150px;width:1000px;display:flex;justify-content:space-between;align-items:center}
.brand-row span{font-weight:700;font-size:19px;color:var(--ink);letter-spacing:.5px}
.brands .arrow{top:152px}
.emblem{left:1128px}

/* footer */
.footer{top:3503px;height:281px;background:var(--footer);color:#c8cfd4}
.emblem-disc{position:absolute;left:528px;top:3378px;width:144px;height:144px;border-radius:50%;background:var(--white)}
.emblem-inner{position:absolute;left:556px;top:3406px;width:88px;height:88px;border-radius:50%;background:var(--blue)}
.foot-head{top:44px;color:var(--white);font-weight:700;font-size:15px;letter-spacing:.5px}
.foot-links{left:102px;top:88px;list-style:none;font-size:12px;line-height:37px}
.foot-links li::before{content:"•";color:var(--white);margin-right:10px}
.contact-block{left:324px;top:86px;font-size:12px;line-height:18px}
.contact-block strong{color:var(--white);font-weight:700;display:block}
.contact-line{display:flex;align-items:center;gap:10px;margin-top:15px}
.contact-line svg{width:14px;height:14px}
.form{left:637px;top:84px;width:260px}
.field{height:33px;background:var(--white);border:1px solid #ccc;margin-bottom:10px;font-size:12px;color:#777;padding:9px 10px}
.field.tall{height:36px}
.submit{width:90px;height:30px;background:var(--blue);color:var(--white);font-weight:700;font-size:15px;display:flex;align-items:center;justify-content:center}
.social{left:989px;top:84px;list-style:none}
.social li{display:flex;align-items:center;gap:10px;font-size:12px;font-weight:700;color:var(--white);height:27px;margin-bottom:11px;letter-spacing:.3px}
.social i{width:26px;height:26px;border-radius:50%;display:block}
.copyright{top:3784px;height:38px;background:var(--blue);color:var(--white);font-size:12px;text-align:center;line-height:38px}
</style>
</head>
<body>

<!-- Header and hero -->
<header class="section hero">
  <div class="hero-photo" role="img" aria-label="Photo of a modern living room with a ceiling heat pump unit and exposed ducting"></div>
  <div class="hero-shade"></div>
  <div class="abs brand">BRAMBLE</div>
  <div class="abs brand-sub">WORKS</div>
  <div class="abs callout">
    <div class="callout-badge">24/7</div>
    <div>
      <div class="callout-num">0800 529 174</div>
      <div class="callout-note">FREE 24/7 SERVICE</div>
    </div>
  </div>
  <nav class="abs nav">
    <a class="active" href="#"><svg viewBox="0 0 28 26"><path d="M3 13 14 3l11 10" fill="none" stroke="currentColor" stroke-width="3"/><path d="M7 12v11h5v-6h4v6h5V12" fill="currentColor"/></svg>HOME</a>
    <a href="#"><svg viewBox="0 0 28 26"><circle cx="11" cy="8" r="5" fill="currentColor"/><path d="M2 24c0-7 4-10 9-10s9 3 9 10z" fill="currentColor"/><circle cx="21" cy="9" r="4" fill="currentColor"/><path d="M19 15c5 0 8 3 8 9h-5" fill="currentColor"/></svg>ABOUT US</a>
    <a href="#"><svg viewBox="0 0 28 26"><circle cx="10" cy="10" r="6" fill="none" stroke="currentColor" stroke-width="3"/><circle cx="20" cy="18" r="4" fill="none" stroke="currentColor" stroke-width="3"/></svg>SERVICES</a>
    <a href="#"><svg viewBox="0 0 28 26"><rect x="3" y="4" width="22" height="18" fill="none" stroke="currentColor" stroke-width="2.5"/><path d="M5 20l7-8 5 5 3-3 4 6z" fill="currentColor"/></svg>PROJECT</a>
    <a href="#"><svg viewBox="0 0 28 26"><path d="M6 3l5 5-3 3c2 4 4 6 8 8l3-3 5 5-4 4C11 24 3 16 2 7z" fill="currentColor"/></svg>CONTACT US</a>
  </nav>
  <div class="abs nav-dot"></div>
  <h1 class="abs hero-title">We Have Installed Thousands Of Heat Pumps And Also Specialise<br>In Diagnostics And Repairs</h1>
  <div class="abs dots"><span></span><span class="on"></span><span></span><span></span></div>
</header>

<!-- Why choose -->
<section class="section why">
  <h2 class="abs title" style="top:38px">WHY CHOOSE <b>BRAMBLE WORKS</b></h2>
  <div class="abs rule" style="top:94px"></div>
  <p class="abs why-intro">Lorem ipsum dolor sit amet, consectetuer adipiscing elit, sed diam nonummy nibh euismod tincidunt ut laoreet dolore magna aliquam erat volutpat. Ut wisi enim ad minim veniam, quis nostrud exerci tation ullamcorper suscipit lobortis nisl.</p>
  <div class="abs why-band"></div>

  <div class="abs why-photo" style="left:102px;background:linear-gradient(150deg,#e6ecef,#aebfca)" role="img" aria-label="Photo of a technician servicing a wall heat pump"></div>
  <div class="abs why-photo" style="left:443px;background:linear-gradient(150deg,#dfe7ec,#9fb3c1)" role="img" aria-label="Photo of a smiling tradesman in a hard hat with a satisfaction badge"></div>
  <div class="abs why-photo" style="left:787px;background:linear-gradient(150deg,#c9d6de,#8fa6b5)" role="img" aria-label="Photo of hands working on outdoor unit pipework"></div>

  <h3 class="abs why-head" style="left:102px">EXPERIENCE COUNTS</h3>
  <h3 class="abs why-head" style="left:443px">SATISFACTION GUARANTEE</h3>
  <h3 class="abs why-head" style="left:787px">LOW PRESSURE SALES</h3>

  <p class="abs why-text" style="left:102px">We have a team of nationally trained and qualified Refrigeration/HVAC/Electrical Engineers and Technicians based in Petone, Wellington offering services to Wellington, Manuwatu and the Wairarapa. We are factory trained and authorised to design, service and install all major brands including Talvoro, Pelnor, Korrowane Electric, Veltrada and Osmelo units. We extend our installation warranty to match that of the manufacturer’s warranty and specialise in our own diagnostics and repair.</p>
  <p class="abs why-text" style="left:443px">We aim to please and I put my name behind our brand! We will take care of your project from start to finish and offer a unique experience with our 100% satisfaction Guarantee*. We will supply and install your system and if your system is not installed how it was explained or not up to a trades standard we will return to make any the necessary modifications free of charge. We back this service up with our 0% upfront strategy, the power is in your hands. We will only invoice you once the installation has been completed up to a BRAMBLE WORKS standard.</p>
  <p class="abs why-text" style="left:787px">Nobody likes the vacuum salesmen’s techniques and neither do we. We will come to your home or business to provide a free measure and quote. Our experience will insure this is a quick and painless experience, you will be provided with expert advice from a qualified Refrigeration Engineer, not a car salesmen turned “Heating Guru”. We will follow up with an email providing our best price straight up, installation details and online brochures. We won’t bug you with repeated phone calls and inbox clogging emails. Once we receive confirmation we will issue you with an installation date and typically have your installation completed within 10 working days.</p>
</section>

<!-- About -->
<section class="section about">
  <h2 class="abs title" style="top:48px">ABOUT <b>BRAMBLE WORKS</b></h2>
  <div class="abs rule" style="top:104px"></div>
  <div class="abs about-img" role="img" aria-label="Cutaway illustration of a house showing ducted heating throughout"></div>
  <p class="abs about-text">Purchasing a Heatpump or Ventilation System can be a significant investment but it doesn't have to be a daunting one. We have a team of nationally trained and qualified Refrigeration/HVAC and Electricians. We are factory trained and authorised to service and install all major brands including Talvoro, Pelnor, Korrowane Electric, Veltrada and Osmelo units. We have installed thousands of heat pumps and also specialise in diagnostics and repairs.</p>
  <span class="btn-outline">READ MORE <svg width="10" height="10" viewBox="0 0 10 10"><path d="M1 1l4 4-4 4M5 1l4 4-4 4" fill="none" stroke="currentColor" stroke-width="1.5"/></svg></span>
</section>

<!-- Services -->
<section class="section services on-blue">
  <h2 class="abs title" style="top:48px">OUR SERVICES</h2>
  <div class="abs rule" style="top:104px"></div>

  <div class="abs svc" style="left:92px">
    <svg class="svc-icon" viewBox="0 0 144 144"><circle cx="72" cy="72" r="70" fill="none" stroke="#fff" stroke-width="3" stroke-dasharray="6 5"/><circle cx="72" cy="72" r="58" fill="#fff"/><rect x="40" y="52" width="64" height="26" rx="4" fill="none" stroke="#33a6d7" stroke-width="4"/><line x1="46" y1="70" x2="98" y2="70" stroke="#33a6d7" stroke-width="3"/><path d="M52 88c4 6-4 10 0 16M72 88c4 6-4 10 0 16M92 88c4 6-4 10 0 16" fill="none" stroke="#33a6d7" stroke-width="3"/></svg>
    <h3>AIR CONDITIONING</h3>
    <p>Heat pumps are the most efficient way of using electricity to heat your home, but some are more efficient than others. We will select.</p>
    <span class="btn-white">READ MORE <svg width="10" height="10" viewBox="0 0 10 10"><path d="M1 1l4 4-4 4M5 1l4 4-4 4" fill="none" stroke="currentColor" stroke-width="1.5"/></svg></span>
  </div>

  <div class="abs svc" style="left:344px">
    <svg class="svc-icon" viewBox="0 0 144 144"><circle cx="72" cy="72" r="70" fill="none" stroke="#fff" stroke-width="3" stroke-dasharray="6 5"/><circle cx="72" cy="72" r="58" fill="#fff"/><rect x="50" y="44" width="44" height="58" fill="#33a6d7"/><g fill="#fff"><rect x="56" y="52" width="8" height="8"/><rect x="68" y="52" width="8" height="8"/><rect x="80" y="52" width="8" height="8"/><rect x="56" y="66" width="8" height="8"/><rect x="68" y="66" width="8" height="8"/><rect x="80" y="66" width="8" height="8"/><rect x="66" y="84" width="12" height="18"/></g></svg>
    <h3>COMMERCIAL</h3>
    <p>We have a growing Portfolio of clients that rely on us for their Commercial requirements. We have proven ourselves to be a force to be.</p>
    <span class="btn-white">READ MORE <svg width="10" height="10" viewBox="0 0 10 10"><path d="M1 1l4 4-4 4M5 1l4 4-4 4" fill="none" stroke="currentColor" stroke-width="1.5"/></svg></span>
  </div>

  <div class="abs svc" style="left:606px">
    <svg class="svc-icon" viewBox="0 0 144 144"><circle cx="72" cy="72" r="70" fill="none" stroke="#fff" stroke-width="3" stroke-dasharray="6 5"/><circle cx="72" cy="72" r="58" fill="#fff"/><g fill="#33a6d7"><rect x="46" y="60" width="9" height="42" rx="4"/><rect x="58" y="60" width="9" height="42" rx="4"/><rect x="70" y="60" width="9" height="42" rx="4"/><rect x="82" y="60" width="9" height="42" rx="4"/><rect x="42" y="66" width="54" height="5"/><rect x="42" y="92" width="54" height="5"/></g><path d="M56 40c4 5-4 9 0 14M72 40c4 5-4 9 0 14M88 40c4 5-4 9 0 14" fill="none" stroke="#33a6d7" stroke-width="3"/></svg>
    <h3>CENTRAL HEATING</h3>
    <p>Ducted Heatpumps are the holy grail of central heating and guess what? They can also cool and dehumidify your home. Ducted Heatpumps.</p>
    <span class="btn-white">READ MORE <svg width="10" height="10" viewBox="0 0 10 10"><path d="M1 1l4 4-4 4M5 1l4 4-4 4" fill="none" stroke="currentColor" stroke-width="1.5"/></svg></span>
  </div>

  <div class="abs svc" style="left:869px">
    <svg class="svc-icon" viewBox="0 0 144 144"><circle cx="72" cy="72" r="70" fill="none" stroke="#fff" stroke-width="3" stroke-dasharray="6 5"/><circle cx="72" cy="72" r="58" fill="#fff"/><g fill="#33a6d7"><path d="M72 72c-6-14-2-28 10-30 8 6 4 22-10 30z"/><path d="M72 72c15-2 27 7 24 19-9 4-21-7-24-19z"/><path d="M72 72c-9 12-24 14-30 4 3-9 19-10 30-4z"/><circle cx="72" cy="72" r="6"/></g></svg>
    <h3>VENTILATION</h3>
    <p>Home ventilation is a very important part of insuring you have a nice dry home to maximise the efficiency of your Heat pump. Whilst HRV.</p>
    <span class="btn-white">READ MORE <svg width="10" height="10" viewBox="0 0 10 10"><path d="M1 1l4 4-4 4M5 1l4 4-4 4" fill="none" stroke="currentColor" stroke-width="1.5"/></svg></span>
  </div>
</section>

<!-- Testimonials -->
<section class="section testimonials">
  <h2 class="abs title" style="top:52px">CLIENTS <b>TESTIMONIALS</b></h2>
  <div class="abs rule" style="top:108px"></div>

  <div class="abs person" style="left:102px"><div class="avatar" role="img" aria-label="Client portrait"></div><div class="person-name">Miss Elna Vorrick</div><div class="person-handle">@vorrick</div></div>
  <div class="abs person" style="left:441px"><div class="avatar" role="img" aria-label="Client portrait"></div><div class="person-name">Miss Tessa Ombray</div><div class="person-handle">@tombray</div></div>
  <div class="abs person" style="left:782px"><div class="avatar" role="img" aria-label="Client portrait"></div><div class="person-name">Miss Dalia Keverin</div><div class="person-handle">@dkeverin</div></div>

  <div class="abs quote current" style="left:102px"><span class="quote-mark">“</span>Lorem wisi enim ad minim veniam, quisl mor nostrni exerci tation ullamcorper this is suskcipit no lobortis nirl nislk ut aliquip.<span class="quote-mark end">”</span><span class="quote-date">4:04PM - AUG 26, 2016</span></div>
  <div class="abs quote" style="left:441px"><span class="quote-mark">“</span>Lorem wisi enim ad minim veniam, quisl mor nostrni exerci tation ullamcorper this is suskcipit no lobortis nirl nislk ut aliquip.<span class="quote-mark end">”</span><span class="quote-date">4:04PM - AUG 27, 2016</span></div>
  <div class="abs quote" style="left:782px"><span class="quote-mark">“</span>Lorem wisi enim ad minim veniam, quisl mor nostrni exerci tation ullamcorper this is suskcipit no lobortis nirl nislk ut aliquip.<span class="quote-mark end">”</span><span class="quote-date">4:04PM - AUG 28, 2016</span></div>

  <div class="abs dots"><span></span><span class="on"></span><span></span></div>
</section>

<!-- Gallery -->
<section class="section gallery">
  <h2 class="abs title" style="top:48px">PROJECTS <b>GALLERY</b></h2>
  <div class="abs rule" style="top:104px"></div>
  <svg class="abs arrow" style="left:52px" viewBox="0 0 20 24"><path d="M15 2 5 12l10 10" fill="none" stroke="#8a9298" stroke-width="2.5"/></svg>
  <div class="abs tile" style="left:97px;background:linear-gradient(150deg,#f1f3f4,#b8c2c8)" role="img" aria-label="Project photo of an outdoor heat pump unit"></div>
  <div class="abs tile" style="left:359px;background:linear-gradient(150deg,#d5dadd,#7d888f)" role="img" aria-label="Project photo of a thermostatic valve">
    <div class="tile-caption"><strong>Lorem wisi enim</strong><span>Lorem wisi enim ad minim veniam, quisl mor nostrni exerci tation ullamcorper</span></div>
  </div>
  <div class="abs tile" style="left:619px;background:linear-gradient(150deg,#eef0ef,#c4c9c5)" role="img" aria-label="Project photo of a relaxed client beneath a wall heat pump"></div>
  <div class="abs tile" style="left:879px;background:linear-gradient(150deg,#e4e8eb,#97a3ab)" role="img" aria-label="Project photo of exposed metal ducting in a ceiling"></div>
  <svg class="abs arrow" style="left:1128px" viewBox="0 0 20 24"><path d="M5 2l10 10-10 10" fill="none" stroke="#8a9298" stroke-width="2.5"/></svg>
</section>

<!-- Brands -->
<section class="section brands">
  <h2 class="abs title" style="top:42px">BRANDS <b>WE SERVE</b></h2>
  <div class="abs rule" style="top:98px"></div>
  <svg class="abs arrow" style="left:58px" viewBox="0 0 20 24"><path d="M15 2 5 12l10 10" fill="none" stroke="#8a9298" stroke-width="2.5"/></svg>
  <div class="abs brand-row">
    <span>Lumavane</span>
    <span>Korrowane Electric</span>
    <span>PELNOR</span>
    <span>Veltrada</span>
    <span>TALVORO</span>
    <span>OSMELO</span>
  </div>
  <svg class="abs arrow" style="left:1122px" viewBox="0 0 20 24"><path d="M5 2l10 10-10 10" fill="none" stroke="#8a9298" stroke-width="2.5"/></svg>
</section>

<!-- Footer -->
<footer class="section footer">
  <h4 class="abs foot-head" style="left:102px">QUICK LINKS</h4>
  <ul class="abs foot-links">
    <li>Home</li><li>About Us</li><li>Services</li><li>Project</li><li>Contact Us</li>
  </ul>

  <h4 class="abs foot-head" style="left:324px">CONTACT DETAILS</h4>
  <div class="abs contact-block">
    <strong>BRAMBLE WORKS</strong>
    27 Harlow Crescent Petone, Wellington
    <div class="contact-line"><svg viewBox="0 0 14 14"><path d="M3 1l3 3-2 2c1 2 2 3 4 4l2-2 3 3-2 2C6 13 1 8 1 3z" fill="#c8cfd4"/></svg>0800 529 174</div>
    <div class="contact-line"><svg viewBox="0 0 14 14"><rect x="3" y="1" width="8" height="12" rx="1.5" fill="none" stroke="#c8cfd4" stroke-width="1.5"/></svg>022 418 6032</div>
    <div class="contact-line"><svg viewBox="0 0 14 14"><rect x="1" y="3" width="12" height="8" fill="none" stroke="#c8cfd4" stroke-width="1.5"/><path d="M1 3l6 5 6-5" fill="none" stroke="#c8cfd4" stroke-width="1.5"/></svg>Marta.k@bramwks.co.nz</div>
  </div>

  <h4 class="abs foot-head" style="left:637px">QUICK CONTACT</h4>
  <div class="abs form">
    <div class="field">Name</div>
    <div class="field">Email</div>
    <div class="field tall">Message</div>
    <div class="submit">Submit</div>
  </div>

  <h4 class="abs foot-head" style="left:989px">FOLLOW US</h4>
  <ul class="abs social">
    <li><i style="background:#3b5b98"></i>FRIENDLANE</li>
    <li><i style="background:#2fa9e0"></i>CHIRPLINE</li>
    <li><i style="background:#1f6fa8"></i>WORKWEAVE</li>
    <li><i style="background:#d2452f"></i>SEARCHPLUS</li>
  </ul>
</footer>
<div class="emblem-disc"></div>
<div class="emblem-inner"></div>
<div class="section copyright">Copyright © 2016 BRAMBLE WORKS. All Rights Reserved.</div>

</body>
</html>
```